Corvanta Group business card redesign

Please throw away what we have and start from scratch. We are bored with our Corvanta Group cards, they need a refresh and as we have introduced a new company to the fold it is the perfect time. Please come up with something that pops. Finishes like foil embossing or engraving are all on the table. Please not be afraid to turn it on it's head. Creative people only.
Target Market(s)
From engineers, to builders, to DIY
Industry/Entity Type
Manufacturer
Contact Information for Business Card
Double sided
Colors
9bcb3c
0255a3
0592cd
Requirements
Must have
- All logos must be shown, the four company logs can be on the back. The group logo is the only one that must be on the front. .
Nice to have
- a design that will age well, we are looking for at least 5 years from the cards.
Should not have
- Please do not send me designs which are just templates that are on the internet, you will be wasting your and my time. As I have searched and searched online and have not found anything I like.

```html
<!DOCTYPE html>
<html lang="en">
<head>
<meta charset="utf-8">
<title>Corvanta Group – Business Card</title>
<link rel="stylesheet" href="https://fonts.googleapis.com/css2?family=Source+Sans+3:wght@400;600;700&display=swap">
<style>
  :root {
    --backdrop: #1b1b1b;
    --card-white: #f3f3f3;
    --brand-navy: #243b80;
    --brand-blue: #0255a3;
    --brand-green: #9bcb3c;
    --brand-cyan: #0592cd;
    --ink: #1e1e1e;
    --strip: #ffffff;
  }
  * { margin: 0; padding: 0; box-sizing: border-box; }
  html, body {
    width: 1200px; height: 899px; overflow: hidden;
    background: var(--backdrop);
    font-family: "Source Sans 3", Arial, sans-serif;
  }
  .stage { position: relative; width: 1200px; height: 899px; }
  .card {
    position: absolute; top: 184px;
    width: 302px; height: 489px;
    border-radius: 11px; overflow: hidden;
  }
  .card--front { left: 299px; background: var(--card-white); }
  .card--back { left: 645px; background: var(--brand-navy); }

  .group-name {
    position: absolute; top: 50px; left: 0; width: 100%;
    text-align: center; font-weight: 700; line-height: 1;
  }
  .group-name__main { display: block; font-size: 38px; letter-spacing: 0.5px; }
  .group-name__sub { display: block; font-size: 13px; letter-spacing: 9px; margin-top: 6px; padding-left: 90px; }
  .card--front .group-name { color: var(--brand-blue); }
  .card--back .group-name { color: #ffffff; }

  .contact { position: absolute; left: 0; width: 100%; text-align: center; color: var(--ink); }
  .contact__name { top: 270px; font-size: 19px; font-weight: 600; color: var(--brand-navy); }
  .contact__role { top: 294px; font-size: 14px; }
  .contact__line { font-size: 14px; }
  .contact__phone1 { top: 338px; }
  .contact__phone2 { top: 358px; }
  .contact__email { top: 378px; }
  .contact__addr1 { top: 420px; }
  .contact__addr2 { top: 436px; }

  .family-strip {
    position: absolute; top: 386px; left: 0; width: 100%; height: 44px;
    background: var(--strip);
  }
  .family-strip__item {
    position: absolute; top: 15px; width: 60px; margin-left: -30px;
    text-align: center; font-size: 11px; font-weight: 700; line-height: 14px;
  }
  .family-strip__item--a { left: 63px; color: var(--brand-green); }
  .family-strip__item--b { left: 124px; color: var(--brand-blue); }
  .family-strip__item--c { left: 185px; color: var(--brand-cyan); }
  .family-strip__item--d { left: 247px; color: var(--brand-navy); }
</style>
</head>
<body>
<main class="stage">
  <section class="card card--front" aria-label="Card front">
    <div class="group-name">
      <span class="group-name__main">CORVANTA</span>
      <span class="group-name__sub">GROUP</span>
    </div>
    <p class="contact contact__name">Daniel Hartley</p>
    <p class="contact contact__role">Managing Director</p>
    <p class="contact contact__line contact__phone1">(044)-456-7890</p>
    <p class="contact contact__line contact__phone2">123-456-7890</p>
    <p class="contact contact__line contact__email">info@youremail.com</p>
    <p class="contact contact__line contact__addr1">12345, Address Goes Here</p>
    <p class="contact contact__line contact__addr2">Country Name, 123456</p>
  </section>

  <section class="card card--back" aria-label="Card back">
    <div class="group-name">
      <span class="group-name__main">CORVANTA</span>
      <span class="group-name__sub">GROUP</span>
    </div>
    <div class="family-strip">
      <span class="family-strip__item family-strip__item--a">Corvanta</span>
      <span class="family-strip__item family-strip__item--b">Brackley</span>
      <span class="family-strip__item family-strip__item--c">Kelso</span>
      <span class="family-strip__item family-strip__item--d">Tarrow</span>
    </div>
  </section>
</main>
</body>
</html>
```